Internationally renowned speaker/campaigner needs a book cover

I need a preliminary cover design for my new book "HALF-LANTERN".

I'm a medical doctor and an internationally renowned speaker and campaigner for human-centered and compassionate healthcare, co-founder of an international social movement PETALS in MEDICINE (http://petalsinmedicine-example.com), and successful author of the book 'ROOM TO LISTEN - Ways to cherish your clients and your work' (http://www.shopvantra-example.com/ROOM-LISTEN-cherish-your-clients/dp/9082614530)

The subtitle of HALF-LANTERN is: "How our one-eyed materialistic science leads to inequality, greed, poverty, violence, ill-health and environmental destruction (and what we can do about it)"

Author: Dr GARETH PELLWICK

Preliminary book blurb:
"As social activists and environmental campaigners we are continuously sabotaging our cause because our strategies are unconsciously supporting the materialistic foundations of our broken world.

Our materialistic science sees the natural world and even people as innate objects, without consciousness or connection. Modern medicine treats patients as broken machines to be fixed, not as conscious, subjective beings. And economic theory says every person is an independent agent, striving to maximize advantage. We turn every human and natural gift into a commodity to be owned, controlled, bought and sold.

Our social policies, education system, justice system and even our democracy assume that incentives, rewards and punishments are the ‘real’ motives for human behavior. Our purpose in life is to ‘get ahead’ and accumulate material goods. Therein lies competition, insecurity, greed, violence, ill-health and the destruction of the natural environment.

Materialistic science is simply blind to the life-world of consciousness, intelligence, purpose and deep interdependence in all natural and human systems. We all know that compassion, kindness, love, and human creativity are the real foundation of our communities, not mindless competition.

But so immersed are we in materialistic assumptions, that in our campaigns we mistakenly adopt tools and strategies from the existing system in our struggle for a better world. But the moment we fight against anything, or demonize our opposition, or sell our ideas for money, or charitably impose our solutions, we only strengthen the material world.

Instead, we have to be the change we want to see: grow an economy of generosity and gifting, freely share ideas, focus on solutions not problems, and deeply believe in the capacity for creativity and healing in every person and every community. You can download this book for free at halflantern-example.org."

Design brief
I need a compelling front page image and title design that conveys the idea that our science is one-eyed or half-blind, hence the title name 'half-lantern', which means half-science.

Our predominant science only sees the material world, not the conscious world. We need both.

I'm also preparing a QUORx talk on the subject and want the compelling image and title to use for this purpose also.

The genre of books is in the class of leadership, entrepreneurs, positive psychology, community development - and I have uploaded some cover images of books in this class. The cover of my current book, ROOM TO LISTEN, has elements of the style I'm looking for: bold, bright, simple, metaphorical, a surprising juxtaposition of technical and human.

The way I develop and market the book will be congruent with the ideas expressed. I will give the e-book away for free and invite people to make a donation if they like it (gift economy). The book will be published on the website unfinished, inviting comments, suggestions, stories and ideas to be included in the finished book. So to a degree, the content of the book will be fully developed by crowdsourcing living examples of the core ideas and creating a community of conversation (including a Chatterbay page). I'll later be looking for a simple WordPress website design based on the book cover graphic, fonts and colours.

So this first design brief and contract is for an e-book cover and later the book will be self-published as a paperback using PressNook.

Target Market(s)

The target audience is readers who are community leaders and social activists - all those utterly passionate about creating a better world, whether it's in the environment, education, healthcare, violence prevention, justice, health communities, etc.

Requirements
Must have
• A compelling image that symbolises the key idea - eyecatching
Should not have
• Must not express 'corporate' concepts, power or hierarchy

```html
<!DOCTYPE html>
<html lang="en">
<head>
<meta charset="utf-8">
<title>HALF-LANTERN — Dr GARETH PELLWICK</title>
<link rel="stylesheet" href="https://fonts.googleapis.com/css2?family=League+Gothic&family=Oswald:wght@300;500;600&display=swap">
<style>
  :root {
    --orange: #e3770f;
    --navy: #1b2a78;
    --paper: #ffffff;
    --blue-deep: #0b2a86;
    --blue-mid: #1566c8;
    --blue-glow: #3fd6f0;
  }
  html, body {
    margin: 0;
    padding: 0;
    width: 750px;
    height: 1200px;
    overflow: hidden;
    background: var(--paper);
  }
  .cover {
    display: block;
    width: 750px;
    height: 1200px;
  }
  .cover-title {
    font-family: "League Gothic", "Oswald", sans-serif;
    fill: var(--orange);
  }
  .cover-subtitle {
    font-family: "Oswald", sans-serif;
    font-weight: 600;
    fill: var(--navy);
  }
  .cover-tagline {
    font-family: "Oswald", sans-serif;
    font-weight: 300;
    fill: var(--orange);
  }
  .author-band { fill: var(--orange); }
  .author-name {
    font-family: "League Gothic", "Oswald", sans-serif;
    fill: var(--paper);
  }
</style>
</head>
<body>
<svg class="cover" viewBox="0 0 750 1200" xmlns="http://www.w3.org/2000/svg">
  <defs>
    <radialGradient id="emblem-tone" cx="50%" cy="45%" r="60%">
      <stop offset="0%" stop-color="var(--blue-glow)"/>
      <stop offset="35%" stop-color="var(--blue-mid)"/>
      <stop offset="100%" stop-color="var(--blue-deep)"/>
    </radialGradient>
  </defs>

  <rect width="750" height="1200" fill="var(--paper)"/>

  <text class="cover-title" x="36" y="232" font-size="250" textLength="678" lengthAdjust="spacingAndGlyphs">HALF-LANTERN</text>

  <rect class="cover-emblem" x="186" y="284" width="378" height="516" rx="150"
        fill="url(#emblem-tone)" role="img"
        aria-label="Profile of a human head inside a large gear, its inner half filled with small turning cogs, in deep and bright blues"/>

  <text class="cover-subtitle" x="80" y="840" font-size="31" textLength="618" lengthAdjust="spacingAndGlyphs">How our one-eyed materialistic science leads to</text>
  <text class="cover-subtitle" x="84" y="880" font-size="31" textLength="612" lengthAdjust="spacingAndGlyphs">INEQUALITY, GREED, POVERTY, VIOLENCE, ILL-HEALTH</text>
  <text class="cover-subtitle" x="180" y="919" font-size="31" textLength="418" lengthAdjust="spacingAndGlyphs">AND ENVIRONMENTAL DESTRUCTION</text>
  <text class="cover-tagline" x="170" y="978" font-size="38" textLength="436" lengthAdjust="spacingAndGlyphs">and what we can do about it</text>

  <rect class="author-band" x="0" y="1072" width="750" height="128"/>
  <text class="author-name" x="105" y="1184" font-size="136" textLength="540" lengthAdjust="spacingAndGlyphs">Dr GARETH PELLWICK</text>
</svg>
</body>
</html>
```